Anzeigengestaltung für einen einen ambulanten Pflegedienst
Zielgruppe
Insgesamt möchte ich gern drei Anzeigen für das Internet gestalten haben. Ich betreibe einen ambulanten Pflegedienst. Die erste Anzeige soll dazu dienen Kunden anzusprechen, die einen Unterstützungsbedarf und / oder einen Beratungsbedarf haben. Die zweite Anzeige soll dazu dienen neues Personal anzuwerben. Die dritte Anzeige soll speziell potenzielle Azubis ansprechen. Die Anzeigen sind gedacht für Tralvio und Pexumora hauptsächlich. In den Druck sollte es schon 10cm x 8cm sein. Es wäre super wenn vielleicht auch eine Art Aufruf an ehrenamtliche Mitarbeiter erfolgt.
Aufgabenstellung
Die Anzeigen sollen den Stil der Homepage beibehalten. Freundlich, frisch und agil wirken. Alle sollten emotional ansprechend sein und gerade der für zukünftige Mitarbeiter sollte deutlich ein gutes Betriebsklima vermitteln. Als Datei habe ich einige Bilder, die bereits für die Homepage oder Flyer verwendet wurden hochgeladen. des Weiteren habe ich die einzelnen Seiten des Flyers hochgeladen.

```html
<!DOCTYPE html>
<html lang="de">
<head>
<meta charset="utf-8">
<title>Team Sorela – Ausbildung Pflege</title>
<link rel="stylesheet" href="https://fonts.googleapis.com/css2?family=Playfair+Display:wght@400&family=Quicksand:wght@500;700&display=swap">
<style>
  :root {
    --teal: #4aaeaa;
    --green: #7cb03a;
    --text-grey: #58585a;
    --band: #edede8;
    --white: #ffffff;
    --ring: #eeeee8;
  }
  * { margin: 0; padding: 0; box-sizing: border-box; }
  html, body { width: 1200px; height: 960px; overflow: hidden; background: var(--white); }
  .ad {
    position: relative;
    width: 1200px;
    height: 960px;
    overflow: hidden;
    background: var(--white);
    font-family: "Quicksand", sans-serif;
  }
  .bottom-band {
    position: absolute;
    left: 0; top: 811px;
    width: 1200px; height: 149px;
    background: var(--band);
  }
  .photo-art {
    position: absolute;
    left: 0; top: 0;
    width: 1200px; height: 960px;
  }
  .brand-badge {
    position: absolute;
    left: 616px; top: 44px;
    width: 242px; height: 242px;
    border-radius: 50%;
    background: var(--white);
    border: 2px solid var(--ring);
    text-align: center;
  }
  .brand-dot {
    position: absolute;
    left: 99px; top: 72px;
    width: 44px; height: 44px;
    border-radius: 50%;
    background: var(--teal);
  }
  .brand-name {
    position: absolute;
    left: 0; right: 0; top: 150px;
    font-family: "Quicksand", sans-serif;
    font-weight: 700;
    font-size: 27px;
    color: var(--text-grey);
    letter-spacing: 0.5px;
  }
  .kicker {
    position: absolute;
    left: 60px; top: 58px;
    font-family: "Playfair Display", serif;
    font-size: 36px;
    color: var(--text-grey);
  }
  .headline {
    position: absolute;
    left: 60px; top: 118px;
    font-family: "Quicksand", sans-serif;
    font-weight: 700;
    font-size: 66px;
    line-height: 75px;
  }
  .headline .line-1 { display: block; color: var(--teal); }
  .headline .line-2 { display: block; color: var(--green); }
  .headline-rule {
    position: absolute;
    left: 60px; top: 288px;
    width: 453px; height: 6px;
    background: var(--green);
  }
  .role-pill {
    position: absolute;
    left: 47px; top: 341px;
    width: 472px; height: 63px;
    border: 3px solid var(--teal);
    border-radius: 32px;
    font-family: "Playfair Display", serif;
    font-size: 36px;
    color: var(--teal);
    text-align: center;
    line-height: 57px;
  }
  .benefits {
    position: absolute;
    left: 60px; top: 455px;
    list-style: none;
    font-family: "Quicksand", sans-serif;
    font-weight: 500;
    font-size: 33px;
    line-height: 47px;
    color: var(--text-grey);
  }
  .benefits li {
    position: relative;
    padding-left: 30px;
    margin-bottom: 12px;
  }
  .benefits li::before {
    content: "+";
    position: absolute;
    left: 0; top: -2px;
    color: var(--green);
  }
  .url-pill {
    position: absolute;
    left: 48px; top: 854px;
    width: 587px; height: 62px;
    border-radius: 31px;
    background: var(--green);
    font-family: "Playfair Display", serif;
    font-size: 31px;
    color: var(--white);
    line-height: 60px;
    padding-left: 27px;
  }
</style>
</head>
<body>
<main class="ad">
  <div class="bottom-band"></div>

  <svg class="photo-art" viewBox="0 0 1200 960" xmlns="http://www.w3.org/2000/svg">
    <defs>
      <linearGradient id="photoTones" x1="0" y1="0" x2="0.3" y2="1">
        <stop offset="0" stop-color="#f3f5f4"/>
        <stop offset="0.45" stop-color="#e2e6e4"/>
        <stop offset="0.62" stop-color="#cfd9e0"/>
        <stop offset="0.78" stop-color="#8dbde9"/>
        <stop offset="1" stop-color="#7ab1e6"/>
      </linearGradient>
    </defs>
    <circle cx="1141" cy="501" r="512" fill="url(#photoTones)" role="img" aria-label="Foto: lächelnde junge Pflegerin in blauer Dienstkleidung"/>
    <path class="arc-teal" d="M591 709 C591 650 622 622 680 622 C712 622 735 627 748 634" fill="none" stroke="var(--teal)" stroke-width="6" stroke-linecap="round"/>
    <path class="arc-green" d="M619 769 C619 700 636 665 690 660 C722 657 752 666 767 676" fill="none" stroke="var(--green)" stroke-width="6" stroke-linecap="round"/>
  </svg>

  <div class="brand-badge">
    <span class="brand-dot"></span>
    <span class="brand-name">TEAM SORELA</span>
  </div>

  <p class="kicker">Junge Talente gesucht!</p>
  <h1 class="headline">
    <span class="line-1">Komm in unser</span>
    <span class="line-2">Team Sorela</span>
  </h1>
  <div class="headline-rule"></div>

  <div class="role-pill">Auszubildende:r Pfleger:in</div>

  <ul class="benefits">
    <li>Ausbildung mit persöhnlichem<br>Ansprechpartnern</li>
    <li>Praxiseinsätze gemeinsam<br>mit der Praxisleitung</li>
    <li>genügend Ruhephasen<br>im Dienstplan</li>
  </ul>

  <div class="url-pill">www.sorela-pflege.de/karriere/</div>
</main>
</body>
</html>
```